ULMIRA card Technical Architecture

Hello everyone ULMIRA: It is a consulting firm in Architecture and Construction. I require a card duplexing, sober, elegant, classic but not boring. Update 1: Use the following data for the card. Name: Gonzalo Pereda Mauricio Villalta Position: COO Twitter: @ulmiraAT Homepage: ulmira-example.com home address not include the participation of all thank you.

Target Market(s)

Construction companies, Architects and Consulting Engineers

Industry/Entity Type

Consulting

Contact Information for Business Card

Los campos que debe tener:
Nombre, Cargo, email, homepage y twitter

Font styles to use
Serif
Sans Serif
Other font styles liked:
• Me gustan playfair display, open sans y roboto, pero estoy sujeto a sus propuestas

Requirements
Must have
• Colors: Present combined proposals in white, red, gray and black Update 1: The two names must be clearly differentiated from the two surnames
Nice to have
• They are free to present their best proposals. I will bring them immediate feedback to the extent you can go see their designs. Complete data for card and logo files will give the winner the

```html
<!DOCTYPE html>
<html lang="es">
<head>
<meta charset="utf-8">
<title>ULMIRA – Tarjeta de visita</title>
<link rel="stylesheet" href="https://fonts.googleapis.com/css2?family=Open+Sans:wght@300;400;600&display=swap">
<style>
  :root {
    --backdrop: #e9e6e4;
    --card-top: #f6f3f3;
    --card-top-edge: #e4dcdc;
    --band-pink: #fa6781;
    --band-pink-deep: #f0566f;
    --band-red: #d0262d;
    --band-red-deep: #b9141b;
    --ink-black: #1d1a1a;
    --ink-red: #b3121a;
    --ink-white: #ffffff;
    --ghost-grey: rgba(60, 50, 50, 0.28);
  }
  * { margin: 0; padding: 0; box-sizing: border-box; }
  html, body { width: 1200px; height: 900px; overflow: hidden; }
  body {
    background: var(--backdrop);
    font-family: "Open Sans", Arial, sans-serif;
    position: relative;
  }
  .card {
    position: absolute;
    width: 556px;
    height: 343px;
    overflow: hidden;
    box-shadow: 0 6px 18px rgba(0, 0, 0, 0.12);
  }
  .card--front { left: 238px; top: 62px; }
  .card--back  { left: 460px; top: 518px; }

  .card__top {
    position: absolute;
    left: 0; top: 0;
    width: 100%; height: 186px;
    background: linear-gradient(180deg, #fbf9f9 0%, var(--card-top) 60%, var(--card-top-edge) 100%);
  }
  .card__band {
    position: absolute;
    left: 0; top: 186px;
    width: 100%; height: 157px;
    background: linear-gradient(180deg,
      var(--band-pink) 0%,
      var(--band-pink-deep) 40%,
      var(--band-red) 52%,
      var(--band-red) 75%,
      var(--band-red-deep) 100%);
  }

  .brand {
    position: absolute;
    left: 0; width: 100%;
    text-align: center;
  }
  .brand__name {
    display: block;
    font-weight: 300;
    font-size: 44px;
    letter-spacing: 12px;
    padding-left: 12px;
    color: var(--ink-black);
    line-height: 1;
  }
  .brand__tagline {
    display: block;
    margin-top: 10px;
    font-weight: 400;
    font-size: 13px;
    letter-spacing: 3.4px;
    color: var(--ink-red);
    text-transform: uppercase;
  }
  .card--front .brand { top: 108px; }

  .card--back .brand { top: 110px; }
  .card--back .brand__name,
  .card--back .brand__tagline { color: var(--ghost-grey); }

  .holder {
    position: absolute;
    right: 324px; top: 241px;
    text-align: right;
    color: var(--ink-white);
  }
  .holder__name { font-weight: 600; font-size: 17px; line-height: 22px; }
  .holder__role { font-weight: 400; font-size: 14px; line-height: 20px; }

  .contact {
    position: absolute;
    left: 277px; top: 226px;
    list-style: none;
    color: var(--ink-white);
    font-size: 14.5px;
    line-height: 20px;
  }
  .contact__item { display: flex; align-items: center; }
  .contact__icon { width: 11px; height: 11px; margin-right: 9px; flex: none; }

  .back-url {
    position: absolute;
    left: 0; top: 262px;
    width: 100%;
    text-align: center;
    color: var(--ink-white);
    font-size: 14.5px;
  }
</style>
</head>
<body>

  <article class="card card--front">
    <div class="card__top"></div>
    <div class="card__band"></div>

    <div class="brand">
      <span class="brand__name">ULMIRA</span>
      <span class="brand__tagline">Arquitectura Técnica</span>
    </div>

    <div class="holder">
      <p class="holder__name">Tomas Ribera</p>
      <p class="holder__role">Managing Director</p>
    </div>

    <ul class="contact">
      <li class="contact__item">
        <svg class="contact__icon" viewBox="0 0 11 11" aria-hidden="true">
          <rect x="2.5" y="0.5" width="6" height="10" rx="1" fill="none" stroke="#fff" stroke-width="1.2"/>
          <rect x="4.5" y="8.3" width="2" height="1" fill="#fff"/>
        </svg>
        555 010 234
      </li>
      <li class="contact__item">
        <svg class="contact__icon" viewBox="0 0 11 11" aria-hidden="true">
          <rect x="1" y="2.5" width="9" height="6.5" fill="#fff"/>
          <path d="M1 2.5 L5.5 6 L10 2.5" fill="none" stroke="#d0262d" stroke-width="0.9"/>
        </svg>
        info@ulmira-example.com
      </li>
      <li class="contact__item">
        <svg class="contact__icon" viewBox="0 0 11 11" aria-hidden="true">
          <circle cx="5.5" cy="5.5" r="5" fill="#fff"/>
          <path d="M0.5 5.5 H10.5 M5.5 0.5 C3 3 3 8 5.5 10.5 M5.5 0.5 C8 3 8 8 5.5 10.5" fill="none" stroke="#d0262d" stroke-width="0.8"/>
        </svg>
        www.ulmira-example.com
      </li>
      <li class="contact__item">
        <svg class="contact__icon" viewBox="0 0 11 11" aria-hidden="true">
          <rect x="0.5" y="0.5" width="10" height="10" rx="1.5" fill="#fff"/>
        </svg>
        @ulmiraAT
      </li>
    </ul>
  </article>

  <article class="card card--back">
    <div class="card__top"></div>
    <div class="card__band"></div>

    <div class="brand">
      <span class="brand__name">ULMIRA</span>
      <span class="brand__tagline">Arquitectura Técnica</span>
    </div>

    <p class="back-url">www.ulmira-example.com</p>
  </article>

</body>
</html>
```